Ward Compass Business Card Design*

We need a business card design for our company Ward Compass. Our company is specialized in providing online consulting services regarding medical institutions, hospitals and doctors. We work with patients worldwide looking to choose between healthcare providers. We have a website you may use as a reference, where we list doctors and clinics worldwide. So we target Medical providers as well as patients worldwide.
Target Market(s)
Medical Providers and patients around the world
Industry/Entity Type
Medical
Contact Information for Business Card
Salwa Kettani
CEO
+90 612 348 2175
info@wardcompass.example
www.wardcompass.example
14 Annakhil 7 H.R.B. Rabat, Morocco
Requirements
Must have
- Company logo/name on one full side, personal info and smaller logo and company name on the other side.
Nice to have
- Smart and elegant design

```html
<!DOCTYPE html>
<html lang="en">
<head>
<meta charset="utf-8">
<title>Ward Compass Business Card</title>
<link rel="stylesheet" href="https://fonts.googleapis.com/css2?family=Poppins:wght@300;400;500;600&display=swap">
<style>
  :root {
    --navy-top: #1b4f78;
    --navy-bottom: #123c66;
    --back-top: #1f4e7f;
    --back-bottom: #143a6c;
    --swoosh-grey: #808080;
    --paper: #ffffff;
    --canvas: #e4e4e4;
    --brand-blue: #173f6e;
    --text-light: #ffffff;
  }
  * { margin: 0; padding: 0; box-sizing: border-box; }
  html, body {
    width: 1200px; height: 1200px; overflow: hidden;
    background: var(--canvas);
    font-family: "Poppins", sans-serif;
  }
  .card {
    position: absolute;
    left: 262px;
    width: 686px;
    height: 392px;
    overflow: hidden;
  }
  .card--front { top: 165px; }
  .card--back {
    top: 653px;
    background: linear-gradient(180deg, var(--back-top), var(--back-bottom));
  }
  .front-art { position: absolute; inset: 0; width: 100%; height: 100%; }
  .holder { position: absolute; left: 32px; top: 28px; color: var(--text-light); }
  .holder-name { font-size: 25px; font-weight: 500; line-height: 1.1; letter-spacing: 0.2px; }
  .holder-role { font-size: 14.5px; font-weight: 400; line-height: 1.3; }
  .contact-list { list-style: none; position: absolute; left: 32px; top: 99px; color: var(--text-light); }
  .contact-list li {
    display: flex; align-items: center; gap: 10px;
    font-size: 15.5px; font-weight: 400; line-height: 19.5px;
  }
  .contact-list svg { width: 13px; height: 13px; flex: none; fill: var(--text-light); }
  .address {
    position: absolute; right: 38px; top: 52px;
    text-align: right; color: var(--text-light);
    font-size: 15.5px; font-weight: 400; line-height: 19.5px;
  }
  .brand-front {
    position: absolute; right: 32px; top: 282px;
    display: flex; align-items: center; gap: 14px;
  }
  .brand-dot {
    width: 34px; height: 34px; border-radius: 50%;
    border: 6px solid var(--brand-blue);
  }
  .brand-name {
    font-size: 26px; font-weight: 600; letter-spacing: 0.5px;
    color: var(--brand-blue);
  }
  .brand-back {
    position: absolute; left: 0; right: 0; top: 118px;
    display: flex; flex-direction: column; align-items: center; gap: 18px;
  }
  .brand-back .brand-dot { width: 60px; height: 60px; border: 10px solid var(--text-light); }
  .brand-back .brand-name { color: var(--text-light); font-size: 34px; }
  .back-url {
    position: absolute; left: 0; right: 0; top: 338px;
    text-align: center; color: var(--text-light);
    font-size: 15px; font-weight: 400; letter-spacing: 4px;
  }
</style>
</head>
<body>
  <section class="card card--front">
    <svg class="front-art" viewBox="0 0 800 457" preserveAspectRatio="none" aria-hidden="true">
      <defs>
        <linearGradient id="frontNavy" x1="0" y1="0" x2="0" y2="1">
          <stop offset="0" stop-color="#1b4f78"/>
          <stop offset="1" stop-color="#0f3a62"/>
        </linearGradient>
      </defs>
      <rect width="800" height="457" fill="url(#frontNavy)"/>
      <path d="M0 340 C240 210 520 158 720 155 L800 160 L800 457 L0 457 Z" fill="#808080"/>
      <path d="M0 392 C250 240 540 170 760 158 L800 162 L800 457 L0 457 Z" fill="#ffffff"/>
    </svg>

    <div class="holder">
      <h1 class="holder-name">Salwa Kettani</h1>
      <p class="holder-role">CEO</p>
    </div>

    <ul class="contact-list">
      <li>
        <svg viewBox="0 0 24 24"><path d="M6.6 10.8a15.1 15.1 0 0 0 6.6 6.6l2.2-2.2a1 1 0 0 1 1-.25 11.4 11.4 0 0 0 3.6.57 1 1 0 0 1 1 1V20a1 1 0 0 1-1 1A17 17 0 0 1 3 4a1 1 0 0 1 1-1h3.5a1 1 0 0 1 1 1c0 1.25.2 2.45.57 3.57a1 1 0 0 1-.25 1z"/></svg>
        +90 612 348 2175
      </li>
      <li>
        <svg viewBox="0 0 24 24"><path d="M2 5h20v14H2z M2 5l10 8 10-8" fill="none" stroke="#fff" stroke-width="0"/><path d="M2 5h20L12 12z M2 7.5l10 7 10-7V19H2z"/></svg>
        info@wardcompass.example
      </li>
      <li>
        <svg viewBox="0 0 24 24"><path d="M12 2a10 10 0 1 0 0 20 10 10 0 0 0 0-20zm-1 17.9A8 8 0 0 1 4.2 10.2L9 15v1a2 2 0 0 0 2 2zm6.9-2.5A2 2 0 0 0 16 16h-1v-3a1 1 0 0 0-1-1H8v-2h2a1 1 0 0 0 1-1V7h2a2 2 0 0 0 2-2v-.4a8 8 0 0 1 2.9 12.8z"/></svg>
        www.wardcompass.example
      </li>
    </ul>

    <p class="address">14 Annakhil 7<br>H.R.B. Rabat, Morocco</p>

    <div class="brand-front">
      <span class="brand-dot"></span>
      <span class="brand-name">WARD COMPASS</span>
    </div>
  </section>

  <section class="card card--back">
    <div class="brand-back">
      <span class="brand-dot"></span>
      <span class="brand-name">WARD COMPASS</span>
    </div>
    <p class="back-url">www.wardcompass.example</p>
  </section>
</body>
</html>
```